Velora Cosmetic Clinic Brochure

I require a high end, luxurious yet natural brochure for my Lumiderm clinic. I prefer the colours blue and silver with white. I was unable to upload the professional images of my clinic but would forward these 9the images were too big).

Target Market(s)

40 to 50 year olds

Industry/Entity Type

Lumiderm and cosmetic treatments

Colors
0054AA
0677BA
7BADD7
CADEEF
E8F1F8

Requirements
Nice to have
• blue and silver colours

```html
<!DOCTYPE html>
<html lang="en">
<head>
<meta charset="utf-8">
<title>Velora Cosmetic Clinic Brochure</title>
<link rel="stylesheet" href="https://fonts.googleapis.com/css2?family=Barlow:wght@400;600;700&family=Barlow+Semi+Condensed:wght@700&family=Oswald:wght@600&family=Pathway+Gothic+One&family=Montserrat:wght@600;700&display=swap">
<style>
  :root{
    --blue-deep:#0054AA;
    --blue-mid:#0677BA;
    --blue-soft:#7BADD7;
    --blue-pale:#CADEEF;
    --blue-mist:#E8F1F8;
    --panel-top:#3FA6E0;
    --silver:#B8B8B8;
    --silver-light:#E2E2E2;
    --white:#FFFFFF;
    --ink:#1D1D1D;
    --stage:#D9D9D9;
  }
  *{margin:0;padding:0;box-sizing:border-box}
  html,body{width:901px;height:1200px;overflow:hidden}
  body{background:var(--stage);position:relative;font-family:"Barlow",sans-serif}

  .spread{position:absolute;left:20px;top:320px;width:861px;height:559px;box-shadow:0 4px 14px rgba(0,0,0,.25);overflow:hidden}

  /* back cover */
  .back{position:absolute;left:0;top:0;width:431px;height:559px;
    background:linear-gradient(160deg,var(--panel-top) 0%,var(--blue-mid) 60%,var(--blue-deep) 100%);color:var(--white)}
  .feature-ring{position:absolute;left:0;top:0}
  .profile-art{position:absolute}
  .contact-block{position:absolute;left:20px;width:250px}
  .section-title{font-family:"Barlow Semi Condensed",sans-serif;font-weight:700;font-size:12.5px;letter-spacing:.2px;line-height:1.1}
  .main-title{font-family:"Barlow Semi Condensed",sans-serif;font-weight:700;font-size:17px;text-decoration:underline;text-underline-offset:3px;text-decoration-thickness:1.5px;position:absolute;left:20px;top:34px}
  .info-line{font-size:10.5px;line-height:13.6px;display:flex;gap:4px}
  .info-line svg{flex:none;margin-top:2px}
  .info-indent{padding-left:14px}
  .body-line{font-size:10.5px;line-height:13.5px}
  .bold-line{font-family:"Barlow Semi Condensed",sans-serif;font-weight:700;font-size:9.6px;line-height:12px}
  .subhead{font-weight:700;font-size:10.5px;line-height:13.5px}
  .divider{position:absolute;left:20px;height:1px;background:rgba(255,255,255,.35)}
  .website{position:absolute;left:20px;top:395px;font-family:"Montserrat",sans-serif;font-weight:700;font-size:12.5px}
  .map-area{position:absolute;left:20px;top:421px;width:227px;height:116px;border-radius:3px;
    background:linear-gradient(135deg,#EEF0F2 0%,#E3E6E8 45%,#CFE6CF 100%)}
  .social{position:absolute;left:280px;top:474px;font-size:9px;line-height:11.6px}
  .social-dots{display:flex;gap:5px;margin-bottom:4px}
  .social-dots span{width:19px;height:19px;border-radius:50%;background:var(--white);display:block}
  .social-label{font-family:"Barlow Semi Condensed",sans-serif;font-weight:700;font-size:9.6px}

  /* front cover */
  .front{position:absolute;left:431px;top:0;width:430px;height:559px;background:var(--white);overflow:hidden}
  .photo-area{position:absolute;right:0;top:60px;width:230px;height:400px;
    background:radial-gradient(ellipse at 60% 45%,#D6D6D6 0%,#EAEAEA 55%,rgba(255,255,255,0) 80%)}
  .brand{position:absolute;right:30px;top:28px;display:flex;align-items:center;gap:8px;font-family:"Barlow",sans-serif;font-weight:400;font-size:30px;color:var(--blue-mid);letter-spacing:1px}
  .brand-dot{width:22px;height:22px;border-radius:50%;background:var(--blue-soft)}
  .brand-sub{position:absolute;right:30px;top:68px;font-family:"Barlow",sans-serif;font-weight:400;font-size:12px;color:var(--blue-mid);letter-spacing:1px}
  .clinic-title{position:absolute;right:20px;top:392px;text-align:right;font-family:"Oswald",sans-serif;font-weight:600;font-size:35px;line-height:37px;color:var(--blue-deep);letter-spacing:-.3px;transform:scaleX(.9);transform-origin:right}
  .tagline{position:absolute;right:20px;top:478px;font-family:"Pathway Gothic One",sans-serif;font-size:19px;color:var(--ink);letter-spacing:.4px}
  .footer-band{position:absolute;left:0;top:515px;width:430px;height:21px;
    background:linear-gradient(90deg,var(--silver) 0%,var(--silver-light) 55%,var(--white) 100%)}
  .footer-url{position:absolute;right:20px;top:519px;font-family:"Montserrat",sans-serif;font-weight:600;font-size:9.5px;letter-spacing:2px;color:var(--ink)}
</style>
</head>
<body>
<main class="spread">

  <section class="back">
    <svg class="feature-ring" width="431" height="559" viewBox="0 0 431 559">
      <circle cx="361" cy="275" r="139" fill="#0A70B8" opacity=".55"/>
      <path d="M 496 228 A 143 143 0 1 0 450 388" fill="none" stroke="var(--silver-light)" stroke-width="7"/>
    </svg>
    <div class="profile-art" role="img" aria-label="Stylised side profile with flowing hair in layered blues"
      style="left:280px;top:150px;width:151px;height:260px;background:linear-gradient(160deg,var(--blue-soft) 0%,#4FA3DC 60%,rgba(79,163,220,0) 100%);border-radius:60% 0 0 40%;opacity:.85"></div>

    <h1 class="main-title">CONTACT US</h1>

    <div class="contact-block" style="top:69px">
      <p class="section-title">CONTACT INFORMATION</p>
      <p class="info-line"><svg width="9" height="9" viewBox="0 0 10 10"><circle cx="5" cy="5" r="5" fill="#fff"/><path d="M3 2.6l1 .1.4 1.2-.6.5a3.4 3.4 0 0 0 1.8 1.8l.5-.6 1.2.4.1 1A4.6 4.6 0 0 1 3 2.6z" fill="var(--blue-mid)"/></svg>Telephone: 0800-555-014</p>
      <p class="info-line"><svg width="9" height="9" viewBox="0 0 10 10"><circle cx="5" cy="5" r="5" fill="#fff"/><rect x="2.4" y="3.2" width="5.2" height="3.6" fill="none" stroke="var(--blue-mid)" stroke-width=".8"/></svg>Email: enquiries@velora.co.nz</p>
      <p class="info-line"><svg width="9" height="9" viewBox="0 0 10 10"><path d="M5 0a4 4 0 0 1 4 4c0 3-4 6-4 6S1 7 1 4a4 4 0 0 1 4-4z" fill="#fff"/><circle cx="5" cy="4" r="1.5" fill="var(--blue-mid)"/></svg>Address: 1/14 Harbour Lane,</p>
      <p class="body-line info-indent">Seaview, Lakeford 8041</p>
    </div>
    <div class="divider" style="top:142px;width:256px"></div>

    <div class="contact-block" style="top:165px">
      <p class="section-title">HOURS OF OPERATION</p>
      <p class="body-line">Our phones are normally answered</p>
      <p class="body-line">between the hours of</p>
      <p class="bold-line" style="margin-top:5px">MONDAY TO FRIDAY 8.00 AM TO 8.00PM</p>
      <p class="bold-line">SATURDAY 8.00 AM TO 4.00 PM</p>
    </div>
    <div class="divider" style="top:245px;width:220px"></div>

    <div class="contact-block" style="top:268px">
      <p class="section-title">APPOINTMENTS</p>
      <p class="subhead">Velora Cosmetic Clinic is open</p>
      <p class="body-line">Monday 8.00 am to 2.00 pm</p>
      <p class="body-line">Tuesday 8.00 am to 2.00 pm</p>
      <p class="body-line">Wednesday 8.00 am to 8.00 pm</p>
      <p class="body-line">Thursday 8.00 am to 8.00 pm</p>
      <p class="body-line">Friday 8.00 am to 2.00 pm</p>
      <p class="body-line">Saturday 8.00 am to 2.00 pm</p>
    </div>
    <div class="divider" style="top:385px;width:236px"></div>

    <p class="website">Website : www.velora.co.nz</p>
    <div class="map-area" role="img" aria-label="Street map showing the clinic location"></div>

    <div class="social">
      <div class="social-dots"><span></span><span></span></div>
      <p class="social-label">SOCIAL MEDIA</p>
      <p>www.friendspage.com/Velora</p>
      <p>www.videohub.com/user/Velora</p>
    </div>
  </section>

  <section class="front">
    <div class="photo-area" role="img" aria-label="Soft greyscale photograph of a smiling mature couple"></div>
    <div class="profile-art" role="img" aria-label="Flowing hair streaks in layered blues sweeping across the cover"
      style="left:0;top:70px;width:400px;height:320px;background:linear-gradient(100deg,#2E8FD4 0%,var(--blue-soft) 45%,rgba(202,222,239,.6) 75%,rgba(255,255,255,0) 100%);border-radius:0 60% 40% 0;opacity:.9"></div>
    <svg width="430" height="559" viewBox="0 0 430 559" style="position:absolute;left:0;top:0">
      <path d="M 0 479 Q 110 470 185 415" fill="none" stroke="var(--silver)" stroke-width="4"/>
      <path d="M 0 50 Q 40 46 75 52" fill="none" stroke="var(--silver)" stroke-width="3"/>
    </svg>
    <div class="brand"><span class="brand-dot"></span>VELORA</div>
    <p class="brand-sub">AESTHETIC DOCTOR</p>
    <h2 class="clinic-title">VELORA MEDICAL<br>COSMETIC CLINIC</h2>
    <p class="tagline">Meticulous approach to natural results</p>
    <div class="footer-band"></div>
    <p class="footer-url">WWW.VELORA.CO.NZ</p>
  </section>

</main>
</body>
</html>
```